Awesome new dental practice requires a New Letterhead design

We would like a new letterhead design to align with our new business branding & business cards. I have uploaded all the logos & current business card details that can be used. The new website can be viewed here https://velortis.com.au

Other useful details: Font Poppins
Colour Palettes:
Dark Pink #c45389
Light Pink: #e83e8c
Black

Please let me know if you have any questions or require anything else.

Dental

• Poppins

```html
<!DOCTYPE html>
<html lang="en">
<head>
<meta charset="utf-8">
<title>Velortis Letterhead</title>
<link href="https://fonts.googleapis.com/css2?family=Poppins:wght@400;500;600&family=Open+Sans:wght@400;600&display=swap" rel="stylesheet">
<style>
  :root {
    --backdrop: #b3b3b3;
    --paper: #fafafa;
    --ink: #111111;
    --body-text: #555555;
    --pink-dark: #c45389;
    --pink-light: #e83e8c;
    --sign-blue: #d6e8f3;
  }
  html, body {
    margin: 0;
    padding: 0;
    width: 1200px;
    height: 1001px;
    overflow: hidden;
    background: var(--backdrop);
  }
  .letterhead {
    position: absolute;
    left: 287px;
    top: 58px;
    width: 625px;
    height: 884px;
    background: var(--paper);
    overflow: hidden;
    font-family: "Open Sans", sans-serif;
    color: var(--body-text);
  }
  .brand {
    position: absolute;
    left: 62px;
    top: 50px;
    display: flex;
    align-items: center;
    gap: 10px;
  }
  .brand-mark {
    width: 14px;
    height: 14px;
    background: var(--pink-dark);
  }
  .brand-name {
    font-family: "Poppins", sans-serif;
    font-weight: 500;
    font-size: 34px;
    line-height: 1;
    color: var(--ink);
  }
  .tagline {
    position: absolute;
    right: 59px;
    top: 67px;
    margin: 0;
    text-align: right;
    font-family: "Poppins", sans-serif;
    font-weight: 600;
    font-size: 13px;
    line-height: 15px;
    color: var(--ink);
  }
  .tagline .accent { color: var(--pink-dark); }
  .letter {
    position: absolute;
    left: 59px;
    top: 200px;
    width: 507px;
    font-size: 9.2px;
    line-height: 16px;
  }
  .salutation { margin: 0 0 32px; }
  .letter p.body-copy {
    margin: 0 0 15.5px;
    text-align: justify;
  }
  .sign-off {
    position: absolute;
    left: 59px;
    top: 580px;
    font-size: 9.2px;
  }
  .sign-name { font-weight: 600; margin: 0; }
  .signature {
    width: 150px;
    height: 32px;
    margin: 10px 0 10px;
    background: var(--sign-blue);
    border-radius: 4px;
  }
  .sign-role { margin: 0; }
  .contact {
    position: absolute;
    left: 34px;
    top: 816px;
    font-family: "Poppins", sans-serif;
    font-size: 10.5px;
    color: var(--ink);
  }
  .contact-address { margin: 0 0 5px; }
  .contact-row {
    display: flex;
    gap: 14px;
    align-items: center;
  }
  .contact-item {
    display: flex;
    align-items: center;
    gap: 6px;
  }
  .contact-icon {
    width: 12px;
    height: 12px;
  }
  .footer-band {
    position: absolute;
    left: 0;
    bottom: 0;
    width: 480px;
    height: 11px;
    background: var(--pink-dark);
  }
  .footer-corner {
    position: absolute;
    right: 0;
    bottom: 0;
    width: 183px;
    height: 22px;
  }
</style>
</head>
<body>
  <main class="letterhead">
    <header>
      <div class="brand">
        <span class="brand-mark"></span>
        <span class="brand-name">Velortis</span>
      </div>
      <p class="tagline">Life is short. <span class="accent">Smile</span> while<br>you still have teeth.</p>
    </header>

    <section class="letter">
      <p class="salutation">Dear Sir,</p>
      <p class="body-copy">Lorem Ipsum is simply dummy text of the printing and typesetting industry. Lorem Ipsum has been the industry's standard dummy text ever since the 1500s, when an unknown printer took a galley of type and scrambled it to make a type specimen book. It has survived not only five centuries, but also the leap into electronic typesetting, remaining essentially unchanged. It was popularised in the 1960s with the release of Letraset sheets containing Lorem Ipsum passages, and more recently with desktop publishing software like Aldus PageMaker including versions of Lorem Ipsum.</p>
      <p class="body-copy">Lorem Ipsum is simply dummy text of the printing and typesetting industry. Lorem Ipsum has been the industry's standard dummy text ever since the 1500s, when an unknown printer took a galley of type and scrambled it to make a type specimen book. It has survived not only five centuries, but also the leap into electronic typesetting, remaining essentially unchanged. It was popularised in the 1960s with the release of Letraset sheets containing Lorem Ipsum passages, and more recently with desktop publishing software like Aldus PageMaker including versions of Lorem Ipsum.</p>
      <p class="body-copy">Lorem Ipsum is simply dummy text of the printing and typesetting industry. Lorem Ipsum has been the industry's standard dummy text ever since the 1500s, when an unknown printer took a galley of type and scrambled it to make a type specimen book.</p>
    </section>

    <section class="sign-off">
      <p class="sign-name">Your Name</p>
      <div class="signature" role="img" aria-label="Handwritten signature"></div>
      <p class="sign-role">CEO &nbsp;|&nbsp; Owner</p>
    </section>

    <footer class="contact">
      <p class="contact-address">Unit 7, 42 Marlow Road Seabrook WA 6790</p>
      <div class="contact-row">
        <span class="contact-item">
          <svg class="contact-icon" viewBox="0 0 12 12" aria-hidden="true"><circle cx="6" cy="6" r="5.5" fill="none" stroke="var(--pink-light)"/><path d="M3.5 5.5h5v2.5h-5z M4.5 5.5l0.5-1.5h2l0.5 1.5" fill="var(--pink-light)"/></svg>
          (08) 9555 0182
        </span>
        <span class="contact-item">
          <svg class="contact-icon" viewBox="0 0 12 12" aria-hidden="true"><circle cx="6" cy="6" r="5.5" fill="none" stroke="var(--pink-light)"/><rect x="3.3" y="4.2" width="5.4" height="3.6" fill="var(--pink-light)"/><path d="M3.3 4.2L6 6.3L8.7 4.2" fill="none" stroke="#fff" stroke-width="0.6"/></svg>
          hello@velortis.com.au
        </span>
        <span class="contact-item">
          <svg class="contact-icon" viewBox="0 0 12 12" aria-hidden="true"><circle cx="6" cy="6" r="5.5" fill="none" stroke="var(--pink-light)"/><circle cx="6" cy="6" r="2.8" fill="none" stroke="var(--pink-light)" stroke-width="0.8"/><path d="M3.2 6h5.6M6 3.2v5.6" stroke="var(--pink-light)" stroke-width="0.6"/></svg>
          www.velortis.com.au
        </span>
      </div>
    </footer>

    <div class="footer-band"></div>
    <svg class="footer-corner" viewBox="0 0 183 22" aria-hidden="true">
      <path d="M0 22 C12 12 16 0 34 0 H183 V22 Z" fill="var(--ink)"/>
    </svg>
  </main>
</body>
</html>
```